Wellness Coach/Personal trainer needs wordpress site/blog with ecommerce capable membership area

We need a WordPress design for FitPennyCoach.com. This is a blog about wellness, weight loss, and health related topics. Design logo will be provided to the winner.

A great site with a design that we would like to emulate are http://qv4.example. The design should be simple, clean, unique, fun, and distinctive. Above all, it should be highly readable and easy to navigate.

These are the specific sections/categories of the blog that should be included and incorporated into the design SEE BELOW.

Thanks in advance for your consideration
Updates

Project Deadline Extended
Reason: I have extended the deadline to evaluate more designs from other pros

Hello all, Please take a minute to review the requirements for this project and please make sure you are capable of meeting ALL the requirements. As you already know I will be making a decision very shortly on whose design I will be moving forward with, if there are any last minute submissions now is the time. Thank you for your time.

Target Market(s)

90 % women 10 % men my clients are usually professionals who value their appearance, health, longevity and time.

Industry/Entity Type

Personal Trainer

Font styles to use
Serif

Colors
886aae
ffcf3e

Requirements
Must have
• Requirements

- start losing weight today.... 555 207 9184 (first line)
- visuals/images and backgrounds to give the idea of wellness, weight loss, healthy living, etc
- navigation menu - home, who we are, what we do, who we serve, blog, contact, members area

1) slider element at top below navigation menu
2) slider element near bottom of page will have testimonials
3) contact form/inquiry form (one page)
4) will provide wellness logo (to give credibility)
5) color scheme purple, gold and white
6) membership area
7) fb, tw, youtube icons
8) footer area - In the footer, there will be smaller company logo, copyright,
disclaimer, privacy policy, terms n conditions, verse of day, and contact info, Phone: (555) 207-9184
Email: support@...
Address:
9) use dummy content/graphic as they will be replaced by real content (the winner will provide instruction on how to make changes to all text and changing graphics)
9) ecommerce enabled / newsletter signup area

```html
<!DOCTYPE html>
<html lang="en">
<head>
<meta charset="utf-8">
<title>FitPenny Coach</title>
<link href="https://fonts.googleapis.com/css2?family=Open+Sans:wght@300;400;600;700&family=Oswald:wght@600&display=swap" rel="stylesheet">
<style>
:root{
  --pink:#c8238e;
  --pink-dark:#a81c77;
  --plum:#9a3b7e;
  --tag:#923f80;
  --purple:#7d2aa0;
  --gold:#e8e23e;
  --ink:#333;
  --muted:#8a8a8a;
  --line:#dcdcdc;
  --band:#f2f2f2;
  --foot:#2a2a2a;
  --foot-low:#212121;
  --foot-text:#bdbdbd;
}
*{box-sizing:border-box;margin:0;padding:0}
html,body{width:1200px;height:3203px;overflow:hidden}
body{position:relative;background:#fff;font-family:"Open Sans",Arial,sans-serif;color:var(--ink)}
.abs{position:absolute}
/* header */
.swatches{left:0;top:0;width:34px}
.swatches span{display:block;height:22px}
.brand{left:0;right:0;top:18px;text-align:center;font-size:40px;font-weight:400;color:var(--pink);letter-spacing:1px}
.nav{left:0;top:90px;width:1200px;height:53px;background:var(--pink);display:flex;padding-left:108px}
.nav a{color:#fff;text-decoration:none;font-size:14px;font-weight:600;line-height:53px;padding:0 25px;margin-right:20px;text-transform:uppercase}
.nav a.active{background:var(--pink-dark)}
/* hero */
.hero{left:0;top:143px;width:1200px;height:657px;background:radial-gradient(ellipse at 50% 40%,#8d8b86 0%,#5e5c58 55%,#3b3a38 100%)}
.hero-arrow{top:445px;width:44px;height:56px;background:rgba(60,60,60,.8);display:flex;align-items:center;justify-content:center}
.callout{left:273px;top:668px;height:54px;display:flex}
.callout .say{background:rgba(40,40,40,.85);color:#fff;font-family:"Oswald",Impact,sans-serif;font-size:30px;line-height:54px;padding:0 18px 0 20px}
.callout .tel{background:var(--gold);color:#222;font-family:"Oswald",Impact,sans-serif;font-size:32px;line-height:54px;padding:0 14px;margin-left:6px}
/* articles */
.h2{font-size:33px;font-weight:400;color:var(--plum);text-transform:uppercase}
.card{width:357px}
.card .img{height:166px;position:relative}
.card .date{position:absolute;left:0;bottom:0;background:rgba(110,110,110,.85);color:#fff;font-size:13px;padding:7px 12px}
.card h3{font-size:16px;font-weight:600;color:var(--plum);line-height:23px;margin-top:16px}
.card p{font-size:13px;color:var(--muted);line-height:19px;margin-top:10px}
.card .share{display:flex;gap:14px;margin-top:12px}
.card .share i{width:15px;height:15px;border-radius:50%;background:#b5b5b5;display:block}
.cats{left:872px;top:882px}
.cats a{display:table;background:var(--tag);color:#fff;text-decoration:none;font-size:15px;padding:0 17px;height:40px;line-height:40px;margin-bottom:7px}
/* testimonials */
.testi{left:0;top:1601px;width:1200px;height:282px;background:linear-gradient(180deg,#4c3d24 0%,#6f5634 45%,#3e3220 100%)}
.testi h2{position:absolute;top:42px;width:100%;text-align:center;font-size:33px;font-weight:400;color:#f0dd3a}
.avatar{left:125px;top:100px;width:130px;height:130px;border-radius:50%;border:4px solid #fff;background:linear-gradient(#cfcfcf,#9a9a9a)}
.quote{left:271px;top:108px;width:810px;color:#eee;font-style:italic;font-size:14px;line-height:26px}
.quote cite{display:block;font-style:normal;color:#f0c53a;font-size:14px;margin-top:4px}
.t-arrow{top:120px}
/* quote form */
.fq{left:0;width:1200px;text-align:center}
.fq h2{font-size:35px;font-weight:600;color:var(--plum)}
.fq p{font-size:14px;color:#555;margin-top:6px}
.field{border:1px solid var(--line);height:33px;font-size:13px;color:#888;padding:0 12px;line-height:31px}
.submit{left:561px;top:2169px;width:78px;height:33px;background:#8e2d72;color:#fff;font-size:14px;font-weight:600;text-align:center;line-height:33px;border-radius:3px}
.rule{left:100px;top:2257px;width:1000px;height:1px;background:var(--line)}
.partners{left:160px;top:2311px;display:flex;gap:48px;align-items:center}
.partners span{display:block;height:40px;background:#c9c9c9;border-radius:4px}
/* membership band */
.member{left:0;top:2402px;width:1200px;height:228px;background:var(--band);text-align:center}
.member h2{margin-top:46px;font-size:33px;font-weight:400;color:#a8458f}
.member p{font-size:16px;color:#555;margin-top:4px}
.btn{display:inline-block;margin-top:16px;background:var(--purple);color:#fff;font-size:18px;font-weight:600;padding:0 22px;height:49px;line-height:49px;border-radius:3px}
.social{left:485px;top:2673px;display:flex;gap:15px}
.social span{width:66px;height:66px;display:block;color:#fff;font-size:11px;font-weight:600;text-align:center;line-height:66px}
/* footer */
.footer{left:0;top:2782px;width:1200px;height:421px;background:var(--foot);color:var(--foot-text)}
.contact-bar{top:36px;width:100%;display:flex;justify-content:center;gap:26px;font-size:15px;color:#ddd;align-items:center}
.contact-bar .sep{color:#999}
.contact-bar svg{vertical-align:-2px;margin-right:6px}
.f-line{top:90px;left:0;width:1200px;height:1px;background:#3b3b3b}
.col{top:128px}
.col h4{font-size:13px;font-weight:600;color:#fff;text-transform:uppercase;margin-bottom:14px}
.col p{font-size:12px;line-height:19px;color:#aaa;width:170px}
.col ul{list-style:none;font-size:12px;line-height:23px;color:#aaa}
.col li::before{content:"• ";color:#888}
.email{width:150px;height:31px;background:#fff;color:#888;font-size:12px;line-height:31px;padding-left:10px;position:relative}
.email b{position:absolute;right:0;top:0;width:42px;height:31px;background:#c9c9c9}
.mini{display:flex;gap:6px;margin-top:14px}
.mini span{width:38px;height:38px;display:block}
.low{top:288px;left:0;width:1200px;height:133px;background:var(--foot-low)}
.disc{left:100px;top:24px;width:610px}
.disc h5{font-size:12px;font-weight:400;color:#ddd}
.disc p{font-size:11px;color:#666;line-height:18px;margin-top:8px}
.f-brand{right:100px;top:20px;font-size:26px;color:#ccc}
.copy{right:190px;top:60px;font-size:12px;color:#ccc;text-align:right;line-height:20px}
.circ{top:66px;width:34px;height:34px;border:2px solid #ccc;border-radius:50%;display:flex;align-items:center;justify-content:center}
</style>
</head>
<body>

<div class="abs swatches" aria-hidden="true">
  <span style="background:#d3259a"></span><span style="background:#b72fb8"></span><span style="background:#d62fd2"></span><span style="background:#f2ec3c"></span><span style="background:#d8cf2a"></span><span style="background:#e8d440"></span>
</div>
<div class="abs brand">FitPenny Coach</div>

<nav class="abs nav">
  <a class="active">Home</a><a>Who we are</a><a>What we do</a><a>Who we serve</a><a>Contact</a><a>Blog</a><a>Members</a>
</nav>

<section class="abs hero" role="img" aria-label="Photo of a man meditating cross-legged against a concrete wall"></section>
<div class="abs hero-arrow" style="left:0"><svg width="14" height="26"><path d="M12 2 2 13l10 11" stroke="#ddd" stroke-width="2" fill="none"/></svg></div>
<div class="abs hero-arrow" style="right:0"><svg width="14" height="26"><path d="M2 2l10 11L2 24" stroke="#ddd" stroke-width="2" fill="none"/></svg></div>
<div class="abs callout"><span class="say">Start losing weight today...</span><span class="tel">555 207 9184</span></div>

<h2 class="abs h2" style="left:100px;top:822px">Latest Articles</h2>
<h2 class="abs h2" style="left:871px;top:822px">Categories</h2>

<article class="abs card" style="left:102px;top:882px">
  <div class="img" role="img" aria-label="Photo of a woman lifting dumbbells" style="background:linear-gradient(135deg,#dfe9ef,#9fc3d6)"><span class="date">Nov 13, 2014</span></div>
  <h3>Pellentesque placerat, odio ac egestas feugiat tristique magna</h3>
  <p>Maecenas a mollis lectus. Morbi lacinia elit non nunc pellentesque, vel accumsan metus sodales. Curabitur varius feugiat tortor, sit amet laoreet.</p>
  <div class="share"><i></i><i></i><i></i><i></i><i></i><i></i></div>
</article>
<article class="abs card" style="left:484px;top:882px">
  <div class="img" role="img" aria-label="Photo of a couple relaxing in a sauna" style="background:linear-gradient(135deg,#8a5a2e,#c68c52)"><span class="date">Nov 13, 2014</span></div>
  <h3>Pellentesque placerat, odio ac egestas feugiat tristique magna</h3>
  <p>Maecenas a mollis lectus. Morbi lacinia elit non nunc pellentesque, vel accumsan metus sodales. Curabitur varius feugiat tortor, sit amet laoreet.</p>
  <div class="share"><i></i><i></i><i></i><i></i><i></i><i></i></div>
</article>
<article class="abs card" style="left:102px;top:1236px">
  <div class="img" role="img" aria-label="Photo of a swimmer doing butterfly stroke" style="background:linear-gradient(135deg,#3aa7d8,#1a6fa8)"><span class="date">Nov 13, 2014</span></div>
  <h3>Pellentesque placerat, odio ac egestas feugiat tristique magna</h3>
  <p>Maecenas a mollis lectus. Morbi lacinia elit non nunc pellentesque, vel accumsan metus sodales. Curabitur varius feugiat tortor, sit amet laoreet.</p>
  <div class="share"><i></i><i></i><i></i><i></i><i></i><i></i></div>
</article>
<article class="abs card" style="left:484px;top:1236px">
  <div class="img" role="img" aria-label="Photo of a runner on a hill at sunset" style="background:linear-gradient(180deg,#f6c46a,#e27a35 60%,#3a2418)"><span class="date">Nov 13, 2014</span></div>
  <h3>Pellentesque placerat, odio ac egestas feugiat tristique magna</h3>
  <p>Maecenas a mollis lectus. Morbi lacinia elit non nunc pellentesque, vel accumsan metus sodales. Curabitur varius feugiat tortor, sit amet laoreet.</p>
  <div class="share"><i></i><i></i><i></i><i></i><i></i><i></i></div>
</article>

<div class="abs cats">
  <a>Weight loss</a><a>Workouts</a><a>Diet</a><a>Wellness</a><a>Healthy living</a><a>Meditation</a><a>Women's health issues</a><a>Kids &amp; Childrens health</a><a>Physiotherapy</a><a>Yoga</a><a>Quisque pretium</a><a>Pellentesque</a><a>Donec rutrum</a><a>Quisque pretium</a>
</div>

<section class="abs testi">
  <h2>Testimonials</h2>
  <div class="abs avatar" role="img" aria-label="Portrait photo of the client"></div>
  <blockquote class="abs quote">“ Nam a malesuada libero. Duis sodales et libero vel interdum. Interdum et malesuada fames ac ante ipsum primis in faucibus. Donec lobortis dui tortor, eu lobortis felis mattis nec. Sed justo quam, luctus eu mauris eget, euismod dapibus sem. Sed tempus feugiat ante, at ornare libero volutpat sed. Maecenas quis magna magna. ”<cite>John Doe, NY</cite></blockquote>
  <svg class="abs t-arrow" style="left:40px" width="16" height="30"><path d="M14 2 2 15l12 13" stroke="#ccc" stroke-width="2.5" fill="none"/></svg>
  <svg class="abs t-arrow" style="right:40px" width="16" height="30"><path d="M2 2l12 13L2 28" stroke="#ccc" stroke-width="2.5" fill="none"/></svg>
</section>

<section class="abs fq" style="top:1930px"><h2>FREE QUOTE</h2><p>Contact you within four hours</p></section>
<div class="abs field" style="left:186px;top:2024px;width:263px">Name</div>
<div class="abs field" style="left:468px;top:2024px;width:263px">E-mail</div>
<div class="abs field" style="left:749px;top:2024px;width:263px">Phone</div>
<div class="abs field" style="left:186px;top:2077px;width:826px;height:64px">Details</div>
<div class="abs submit">SUBMIT</div>

<div class="abs rule"></div>
<div class="abs partners" aria-label="Partner badges">
  <span style="width:100px"></span><span style="width:115px"></span><span style="width:135px"></span><span style="width:90px"></span><span style="width:110px"></span><span style="width:160px"></span>
</div>

<section class="abs member">
  <h2>Aliquam in consectetur sapien</h2>
  <p>Aliquam nunc mauris, vestibulum id justo euismod rutrum dolor molestie nisi.</p>
  <span class="btn">GET A MEMBERSHIP NOW</span>
</section>

<div class="abs social">
  <span style="background:#3b5a9a">Share</span><span style="background:#2aa3e0">Follow</span><span style="background:#d9302a">Watch</span>
</div>

<footer class="abs footer">
  <div class="abs contact-bar">
    <span><svg width="13" height="14"><path d="M3 1l3 3-2 2c1 2 2 3 4 4l2-2 3 3-2 2C6 13 1 8 1 3z" fill="#ddd"/></svg>Contact us today! (555) 207-9184</span>
    <span class="sep">|</span>
    <span><svg width="11" height="15"><path d="M5.5 0A5 5 0 0 0 .5 5c0 4 5 10 5 10s5-6 5-10a5 5 0 0 0-5-5zm0 7a2 2 0 1 1 0-4 2 2 0 0 1 0 4z" fill="#ddd"/></svg>55 Building name, Street name, City - Zipcode</span>
    <span class="sep">|</span>
    <span><svg width="15" height="11"><rect width="15" height="11" fill="#ddd"/><path d="M0 0l7.5 6L15 0" stroke="#2a2a2a" fill="none"/></svg>support@fitpennycoach.com</span>
  </div>
  <div class="abs f-line"></div>
  <div class="abs col" style="left:128px"><h4>Verse of day</h4><p>Donec euismod ligula a ex cursus semper. Vestibulum aliquam mi eu dui porta eleifend. Integer at inter-dum purus.</p></div>
  <div class="abs col" style="left:384px"><h4>Navigation</h4><ul><li>Who we are</li><li>What we do</li><li>Who we serve</li><li>Contact</li><li>blog</li></ul></div>
  <div class="abs col" style="left:551px"><h4>Membership</h4><ul><li>Register</li><li>Login</li><li>Newsletter</li><li>Privacy policy</li><li>Terms and conditions</li></ul></div>
  <div class="abs col" style="left:730px"><h4>Other links</h4><ul><li>Disclaimer</li><li>Sitemap</li><li>Help</li></ul></div>
  <div class="abs col" style="left:886px"><h4>Newsletter</h4><div class="email">E-mail<b></b></div>
    <div class="mini"><span style="background:#3b5a9a"></span><span style="background:#2aa3e0"></span><span style="background:#d9302a"></span></div></div>
  <div class="abs low">
    <div class="abs disc"><h5>Disclaimer</h5><p>Vivamus a risus at eros auctor auctor. Quisque id risus ante. Curabitur sed erat lorem. Duis ut augue sed ante tempus condimentum vitae quis nisl. Integer sit amet sagittis ligula. Sed a nibh lacinia leo ornare viverra non nec felis. Fusce vel dolor et nibh sodales placerat.</p></div>
    <div class="abs f-brand">FitPenny Coach</div>
    <div class="abs copy">Copyright © 2014 FitPenny Coach.<br>All rights reserved.</div>
    <div class="abs circ" style="right:144px"><svg width="16" height="11"><rect width="16" height="11" fill="#ccc"/><path d="M0 0l8 6 8-6" stroke="#212121" fill="none"/></svg></div>
    <div class="abs circ" style="right:100px"><svg width="14" height="14"><path d="M7 2v11M2 7l5-5 5 5" stroke="#ccc" stroke-width="2" fill="none"/></svg></div>
  </div>
</footer>

</body>
</html>
```